" O Instituto Raiz Aberta tem como alicerce o fortalecimento e empoderamento do movimento que gere autonomia para a vida Consolidada há 20 anos num modelo de atuação multidisciplinar que desenvolve estratégias voltadas a promoção de uma vida sustentável e funcional. Nesse sentido consolidamos um trabalho junto a população menos favorecida e em vulnerabilidade social buscando estratégias de impacto nos eixos de atividade física, educação, cultura e lazer que capacitem o protagonismo de suas vidas. Para tanto atuamos com planejamento estratégico e ações práticas voltados a seguinte demanda: 1. Combate a Obesidade Infato Juvenil 2. Programa voltado a dependentes quimicos 3. Combate ao sedentarismo e obesidade 4. Programa voltado ao Envelhecimento Sustentável 5. Programa de inclusão através de atividades artisticas Entre outros "

```html
<!DOCTYPE html>
<html lang="pt-BR">
<head>
<meta charset="UTF-8">
<title>Papel Timbrado — Instituto Raiz Aberta</title>
<link href="https://fonts.googleapis.com/css2?family=Montserrat:wght@500;600;700&display=swap" rel="stylesheet">
<style>
  :root {
    --stage: #e9ebec;
    --paper: #ffffff;
    --brand-navy: #1f5a7a;
    --brand-teal: #3f9aa8;
    --band-light: #9cc3cc;
    --band-dark: #6fa6b4;
    --band-edge: #4e9aa8;
    --on-band: #ffffff;
  }
  * { margin: 0; padding: 0; box-sizing: border-box; }
  html, body {
    width: 1200px;
    height: 1200px;
    overflow: hidden;
    background: var(--stage);
    font-family: "Montserrat", sans-serif;
  }
  .canvas {
    width: 1200px;
    height: 1200px;
    display: flex;
    align-items: center;
    justify-content: center;
  }
  .letterhead {
    position: relative;
    width: 778px;
    height: 1100px;
    background: var(--paper);
    box-shadow: 0 6px 24px rgba(0, 0, 0, 0.12);
    overflow: hidden;
  }
  .letterhead__brand {
    position: absolute;
    top: 70px;
    left: 80px;
    display: flex;
    align-items: center;
    gap: 14px;
  }
  .brand__dot {
    width: 34px;
    height: 34px;
    border-radius: 50%;
    background: var(--brand-teal);
  }
  .brand__name {
    font-size: 21px;
    font-weight: 700;
    color: var(--brand-navy);
    letter-spacing: 0.02em;
    white-space: nowrap;
  }
  .letterhead__footer {
    position: absolute;
    left: 0;
    bottom: 0;
    width: 100%;
    height: 140px;
  }
  .footer__wave {
    position: absolute;
    inset: 0;
    width: 100%;
    height: 100%;
  }
  .footer__content {
    position: absolute;
    left: 0;
    right: 0;
    bottom: 24px;
    display: flex;
    flex-direction: column;
    align-items: center;
    gap: 14px;
    color: var(--on-band);
  }
  .footer__tagline {
    font-size: 15px;
    font-weight: 700;
  }
  .footer__social {
    display: flex;
    align-items: center;
    gap: 8px;
    font-size: 11px;
    font-weight: 500;
  }
  .social__mark {
    width: 14px;
    height: 14px;
    border-radius: 50%;
    background: var(--on-band);
  }
</style>
</head>
<body>
  <main class="canvas">
    <article class="letterhead">
      <header class="letterhead__brand">
        <span class="brand__dot"></span>
        <span class="brand__name">Instituto Raiz Aberta</span>
      </header>

      <footer class="letterhead__footer">
        <svg class="footer__wave" viewBox="0 0 778 140" preserveAspectRatio="none" aria-hidden="true">
          <defs>
            <linearGradient id="bandFill" x1="0" y1="0" x2="1" y2="0">
              <stop offset="0" stop-color="#6fa6b4"/>
              <stop offset="0.5" stop-color="#9cc3cc"/>
              <stop offset="1" stop-color="#6fa6b4"/>
            </linearGradient>
          </defs>
          <path d="M0 40 Q389 -10 778 40 L778 140 L0 140 Z" fill="url(#bandFill)"/>
          <path d="M0 34 Q389 -16 778 34" fill="none" stroke="#4e9aa8" stroke-width="3"/>
        </svg>
        <div class="footer__content">
          <p class="footer__tagline">Fortalecendo Raízes!</p>
          <p class="footer__social"><span class="social__mark"></span>@institutoraizaberta</p>
        </div>
      </footer>
    </article>
  </main>
</body>
</html>
```